Website Comps for Famous Southern BBQ Restaurant in Alabama

We need an authentic, brand-focused redesign for a restaurant.

We need an authentic look.
The client really likes this website.
https://pelmarsmokehouse.example/

I don't want to see a bunch of crazy colors.
Avoid image sliders on the homepage. I hate those.

Please mockup the following three pages:
Homepage
Interior page (for mockup purposes, you can do an About page)
Menu page

I only need the PSD's; not the website coded.

Here is the current website: www.kortiespit.example

https://pelmarsmokehouse.example/

Here are some additional stock photos. New photos will be shot, but these may help for your mock-up designs.
https://files.quillbox.example/sh/83kkqvtrd41zpa7/XQM20PbT9LyRk-wnEuvJ3tpd?dl=0
Updates

I realize we don't have a lot of high-quality photos to work with.Those will be shot.Here are some additional stock photos that may help.https://files.quillbox.example/sh/83kkqvtrd41zpa7/XQM20PbT9LyRk-wnEuvJ3tpd?dl=0 Added Saturday, June 10, 2017

Target Market(s)

United states

Industry/Entity Type

Restaurant

Number of Pages Required

3 page

Font styles to use
Sans Serif

Colors

Designer to choose colors to be used in the design.

Requirements
Must have
• An authentic look.
• The client really likes this website.
• https://pelmarsmokehouse.example/
• It's simple, bold, and vintage at the same time.
• That is what we want.
• Our existing website is
• kortiespit.example
Nice to have
• Simplicity. Something that makes the food look good.
• Possibly a background.
• Logo:
• https://files.quillbox.example/s/t62bnezwhk0qpl3/kories-pit-lakeview.png?dl=0
• Here is a sampling of photos for your comps:
• https://files.quillbox.example/sh/59ryhdupqv2ncmx/MPT4c1ZLvWeQjHoNUyrA8BfxKs?dl=0
Should not have
• Nothing too busy.
• Not too many colors.
• Keep it simple, authentic, "down home."
• No homepage image sliders.

```html
<!DOCTYPE html>
<html lang="en">
<head>
<meta charset="utf-8">
<title>Kortie's Pit — Home</title>
<link rel="stylesheet" href="https://fonts.googleapis.com/css2?family=Lato:wght@300;400;700;900&display=swap">
<style>
:root{
  --brown:#4b1800;
  --cream:#f1e9df;
  --red:#e0393f;
  --orange:#f4a21f;
  --tan:#b48b5c;
  --ink:#2b2b2b;
  --grey:#777;
  --line:#d9d4cf;
  --white:#fff;
}
*{box-sizing:border-box;margin:0;padding:0}
html,body{width:1200px;height:2390px;overflow:hidden}
body{position:relative;background:var(--cream);font-family:'Lato',sans-serif;color:var(--ink)}
.abs{position:absolute}

/* header */
.site-header{left:0;top:0;width:1200px;height:108px;background:var(--brown)}
.brand{left:88px;top:22px;color:var(--orange);font-weight:900;font-size:22px;line-height:24px;letter-spacing:1px}
.main-nav{right:86px;top:46px;display:flex;gap:32px}
.main-nav a{color:var(--white);text-decoration:none;font-size:13px;text-transform:uppercase;letter-spacing:.2px}

/* hero */
.hero-photo{left:0;top:108px;width:1200px;height:343px;background:linear-gradient(100deg,#5a3a22 0%,#8a6444 35%,#9c7a58 60%,#7d5c40 100%)}

.welcome{left:0;top:500px;width:1200px;text-align:center;color:var(--red);font-size:48px;font-weight:400}
.feature-photo{left:86px;top:604px;width:1028px;height:390px;background:linear-gradient(90deg,#3b2a20 0%,#b4824f 40%,#7b4a2c 70%,#3f3a22 100%)}

/* menus */
.menu-intro{left:86px;top:994px;width:320px;height:496px;background:var(--brown);text-align:center;color:var(--orange);font-weight:700}
.menu-intro .name{margin-top:188px;font-size:35px}
.menu-intro .label{margin-top:14px;font-size:25px;line-height:35px}
.menu-body{left:406px;top:994px;width:708px;height:496px;background:var(--white)}
.menu-tabs{left:435px;top:1037px;list-style:none}
.menu-tabs li{height:34px;line-height:32px;font-size:13px;font-weight:700;color:#333;padding-left:15px}
.menu-tabs li.active{color:var(--white);background:var(--orange);width:139px;clip-path:polygon(0 0,88% 0,100% 50%,88% 100%,0 100%)}
.menu-list{left:607px;top:1037px;width:478px;height:244px;border:1px solid var(--line);padding:35px 27px 0 27px}
.dish{display:flex;justify-content:space-between;font-size:13px;color:#666;margin-bottom:22px}
.dish small{display:block;font-size:10px;margin-top:4px}
.dish .price{font-weight:700;color:#555}

/* news */
.section-title{left:0;top:1568px;width:1200px;text-align:center;color:var(--red);font-size:35px;font-weight:400}
.news-card{top:1652px;width:494px;height:205px;background:var(--white);border:1px solid #cfc8c0;display:flex}
.news-photo{width:233px;height:203px;position:relative;flex:none}
.news-date{position:absolute;right:0;top:0;background:var(--brown);color:var(--white);display:flex;align-items:center;gap:3px;padding:4px 6px}
.news-date .day{font-size:28px}
.news-date .mo{font-size:11px;line-height:12px}
.news-text{padding:20px 12px 0 9px;width:259px}
.news-text h3{font-size:12.5px;font-weight:700;line-height:19px;color:#222}
.news-text p{font-size:12px;line-height:18px;color:var(--grey);margin-top:10px;height:54px;overflow:hidden}
.news-text .more{display:block;margin-top:18px;font-size:12px;color:#444;text-decoration:none}

/* contact band */
.info-band{left:0;top:1954px;width:1200px;height:89px;background:var(--orange)}
.info-item{top:0;height:89px;display:flex;align-items:center;gap:14px;color:var(--white);font-size:17px;white-space:nowrap}
.info-item .ico{width:34px;height:34px;border-radius:50%;background:var(--tan);display:flex;align-items:center;justify-content:center;flex:none}

/* footer */
.site-footer{left:0;top:2043px;width:1200px;height:347px;background:var(--brown)}
.footer-brand{left:92px;top:2142px;color:var(--orange);font-weight:900;font-size:20px;line-height:22px;width:92px;text-align:center}
.footer-about{left:204px;top:2112px;width:222px;font-size:12px;line-height:20px;color:#d6c3b6}
.divider{width:1px;top:2088px;height:178px;background:#7a4a33}
.footer-title{top:2084px;color:var(--white);font-size:17px;font-weight:400}
.field{left:484px;width:254px;height:45px;background:var(--white);font-size:11px;color:#444;padding:17px 28px}
.subscribe{left:484px;top:2242px;width:254px;height:50px;border-radius:25px;background:var(--orange);color:var(--white);font-size:21px;text-align:center;line-height:50px}
.sitemap{top:2134px;list-style:none}
.sitemap li{font-size:12px;line-height:22.5px;color:#e7dbd2}
.footer-rule{left:86px;top:2323px;width:1028px;height:1px;background:#6b3a22}
.copyright{left:88px;top:2348px;font-size:11px;color:#d6c3b6}
.social{left:1024px;top:2344px;display:flex;gap:20px}
.social span{width:16px;height:16px;border-radius:50%;background:#e7dbd2}
</style>
</head>
<body>

<header class="site-header abs">
  <div class="brand abs">KORTIE'S<br>PIT</div>
  <nav class="main-nav abs">
    <a href="#">Home</a><a href="#">About</a><a href="#">Locations</a><a href="#">Restaurant Menus</a><a href="#">Catering</a><a href="#">News</a><a href="#">Store</a><a href="#">Contact Us</a>
  </nav>
</header>

<div class="hero-photo abs" role="img" aria-label="Weathered wooden restaurant sign reading cold beer, with a beer bottle in the foreground"></div>

<h1 class="welcome abs">Welcome to KORTIE'S PIT</h1>
<div class="feature-photo abs" role="img" aria-label="Close-up of a loaded barbecue burger beside deviled eggs"></div>

<section>
  <div class="menu-intro abs">
    <div class="name">KORTIE'S PIT</div>
    <div class="label">RESTAURANT<br>MENUS</div>
  </div>
  <div class="menu-body abs"></div>
  <ul class="menu-tabs abs">
    <li class="active">Sandwiches</li><li>Plates</li><li>Ribs</li><li>Dogs</li><li>Stuffed Taters</li><li>Sides</li><li>Kortie's To Go</li><li>Kids</li><li>Drinks</li><li>Sauce</li><li>Desserts</li>
  </ul>
  <div class="menu-list abs">
    <div class="dish"><div>Kortie's Original Pulled Pork<small>(add slaw .50)</small></div><div class="price">$6.25</div></div>
    <div class="dish"><div>Smoked Chicken with White BBQ Sauce<small>(add slaw .50)</small></div><div class="price">$6.25</div></div>
    <div class="dish"><div>Combo (sandwich, 1 side &amp; drink)</div><div class="price">$10.50</div></div>
  </div>
</section>

<h2 class="section-title abs">Our News</h2>

<article class="news-card abs" style="left:86px">
  <div class="news-photo" role="img" aria-label="Baked potato stuffed with pulled pork and barbecue sauce" style="background:linear-gradient(135deg,#6a2a14,#a5532a 50%,#c9b9a0)">
    <div class="news-date"><span class="day">09</span><span class="mo">March<br>2017</span></div>
  </div>
  <div class="news-text">
    <h3>Pork-Stuffed Tater Makes the List of “100 Plates to Try in the South”</h3>
    <p>The “Pork-Stuffed Tater” is listed as one of the State Tourism Bureau's 100 Plates to Try in the South Before You Go.</p>
    <a class="more" href="#">Read More &gt;</a>
  </div>
</article>

<article class="news-card abs" style="left:618px">
  <div class="news-photo" role="img" aria-label="Pulled pork sandwich with a bowl of baked beans" style="background:linear-gradient(135deg,#d7c4a8,#8a5a34 55%,#5a2a12)">
    <div class="news-date"><span class="day">10</span><span class="mo">March<br>2017</span></div>
  </div>
  <div class="news-text">
    <h3>Trail &amp; Table Monthly Names Kortie's “Best Barbecue in America”</h3>
    <p>Trail &amp; Table Monthly recently called Kortie's Pit in Lakeview the “Best Barbecue in America.” “If you're eager to try out the</p>
    <a class="more" href="#">Read More &gt;</a>
  </div>
</article>

<div class="info-band abs">
  <div class="info-item abs" style="left:131px">
    <span class="ico"><svg width="16" height="16" viewBox="0 0 24 24"><path fill="#fff" d="M6.6 10.8a15.1 15.1 0 0 0 6.6 6.6l2.2-2.2a1 1 0 0 1 1-.25 11.4 11.4 0 0 0 3.6.57 1 1 0 0 1 1 1V20a1 1 0 0 1-1 1A17 17 0 0 1 3 4a1 1 0 0 1 1-1h3.5a1 1 0 0 1 1 1c0 1.25.2 2.45.57 3.6a1 1 0 0 1-.25 1z"/></svg></span>
    (205) 555-0148
  </div>
  <div class="info-item abs" style="left:370px">
    <span class="ico"><svg width="14" height="18" viewBox="0 0 24 30"><path fill="#fff" d="M12 0a10 10 0 0 0-10 10c0 7.5 10 20 10 20s10-12.5 10-20A10 10 0 0 0 12 0zm0 14a4 4 0 1 1 0-8 4 4 0 0 1 0 8z"/></svg></span>
    2214 Larkmoor Road, Lakeview AL 35290
  </div>
  <div class="info-item abs" style="left:786px">
    <span class="ico"><svg width="18" height="18" viewBox="0 0 24 24"><circle cx="12" cy="12" r="9" fill="none" stroke="#fff" stroke-width="2.4"/><path d="M12 7v5l3 2" fill="none" stroke="#fff" stroke-width="2.4" stroke-linecap="round"/></svg></span>
    Mon — Sat: 11 AM — 8 PM
  </div>
</div>

<footer class="site-footer abs"></footer>
<div class="footer-brand abs">KORTIE'S PIT</div>
<p class="footer-about abs">Lorem ipsum dolor sit amet, consectetur adipiscing elit, sed do eiusmod tempor incididunt ut labore et dolore magna aliqua. Ut enim ad minim veniam, quis nostrud exercitation ...</p>
<div class="divider abs" style="left:435px"></div>
<h4 class="footer-title abs" style="left:486px">Join Our Newsletter</h4>
<div class="field abs" style="top:2127px">Name</div>
<div class="field abs" style="top:2183px">Email</div>
<div class="subscribe abs">SUBSCRIBE</div>
<div class="divider abs" style="left:822px"></div>
<h4 class="footer-title abs" style="left:877px">Sitemap</h4>
<ul class="sitemap abs" style="left:878px"><li>Home</li><li>About</li><li>Locations</li><li>Restaurant Menus</li></ul>
<ul class="sitemap abs" style="left:1013px"><li>Catering</li><li>News</li><li>Store</li><li>Contact Us</li></ul>
<div class="footer-rule abs"></div>
<p class="copyright abs">Copyright © 2017 Kortie's Pit, LLC. All Rights Reserved.</p>
<div class="social abs" role="img" aria-label="Social media links"><span></span><span></span><span></span></div>

</body>
</html>
```